Kelvor Engineers: Why you should hire us keepsake

New design. Open to plastic cards. We are an engineering firm that designs cell phone towers and commercial buildings. Please check out our website www.kelvorstruct.com for more details. We want people to remember our card and for it to be useful if possible. We want the same look and feel on these cards to be translated to other marketing material we may need such as brochures.

Target Market(s)

Architects, Developers and Telecommunication Carriers

Industry/Entity Type

Engineering

Contact Information for Business Card

Card with our company colors, logo, and innovative design with elements related to our industry.

Font styles to use
Sans Serif

Colors
9bcb3c
abd036
0255a3

Requirements
Must have
• Sleek and hip design
Nice to have
• Bright lime green and navy coloring that pops with an innovative design.
Should not have
• A basic and boring design

```html
<!DOCTYPE html>
<html lang="en">
<head>
<meta charset="utf-8">
<title>Kelvor Engineers – Business Card</title>
<link rel="stylesheet" href="https://fonts.googleapis.com/css2?family=Work+Sans:wght@400;500;600;800&display=swap">
<style>
  :root{
    --navy:#1b2f63;
    --navy-deep:#15254f;
    --lime:#c3c72a;
    --white:#ffffff;
    --ink:#1b2f63;
    --backdrop:#1d1d1f;
  }
  *{margin:0;padding:0;box-sizing:border-box}
  html,body{width:1200px;height:963px;overflow:hidden;background:var(--backdrop)}
  body{font-family:"Work Sans",sans-serif;position:relative}
  .card{position:absolute;left:320px;width:560px;height:320px;border-radius:18px;overflow:hidden;box-shadow:0 18px 40px rgba(0,0,0,.5)}
  .card--front{top:120px;background:var(--white)}
  .card--back{top:500px;background:var(--navy)}

  .front__brand{position:absolute;left:40px;top:44px;font-weight:800;font-size:66px;letter-spacing:-1px;color:var(--lime);line-height:1}
  .front__swoosh{position:absolute;left:0;top:0;width:560px;height:320px}
  .tagline{font-family:"Work Sans",sans-serif;font-size:10.5px;font-weight:500;letter-spacing:1.4px;fill:var(--white)}

  .contact{position:absolute;left:300px;top:120px;width:230px;color:var(--ink)}
  .contact__name{font-weight:600;font-size:17px}
  .contact__title{font-size:12px;color:var(--lime);margin-top:1px}
  .contact__rule{height:1.5px;background:var(--navy);margin:7px 0 8px}
  .contact__list{list-style:none;font-size:12.5px;line-height:17px}
  .contact__list li{display:flex;align-items:center;gap:8px}
  .contact__list svg{width:10px;height:10px;flex:none}

  .back__brand{position:absolute;left:0;right:0;top:70px;text-align:center;font-weight:800;font-size:110px;letter-spacing:-2px;color:var(--lime);line-height:1}
  .back__cities{position:absolute;left:0;right:0;bottom:58px;text-align:center;color:var(--white);font-size:15px;font-weight:500;letter-spacing:1.6px}
  .back__cities .sep{color:var(--lime);margin:0 6px}
</style>
</head>
<body>
  <section class="card card--front" aria-label="Business card front">
    <svg class="front__swoosh" viewBox="0 0 560 320">
      <path d="M0,150 C180,250 380,280 560,300 L560,320 L0,320 Z" fill="var(--navy)"/>
      <path d="M0,135 C185,235 385,266 560,290" fill="none" stroke="var(--lime)" stroke-width="5"/>
      <path id="taglinePath" d="M175,286 C290,298 400,304 520,310" fill="none"/>
      <text class="tagline"><textPath href="#taglinePath">MULTI-DISCIPLINE ENGINEERING</textPath></text>
    </svg>
    <div class="front__brand">Kelvor</div>
    <div class="contact">
      <div class="contact__name">Dana Whitfield Moreau</div>
      <div class="contact__title">Director</div>
      <div class="contact__rule"></div>
      <ul class="contact__list">
        <li><svg viewBox="0 0 10 10"><path d="M2,1 L4,1 L4.6,3 L3.4,3.8 C4,5.2 4.8,6 6.2,6.6 L7,5.4 L9,6 L9,8 C5,9 1,5 2,1 Z" fill="var(--lime)"/></svg>555.210.4417</li>
        <li><svg viewBox="0 0 10 10"><rect x="2.5" y="0.5" width="5" height="9" rx="1" fill="none" stroke="var(--lime)"/></svg>555.388.1920</li>
        <li><svg viewBox="0 0 10 10"><rect x="0.5" y="2" width="9" height="6" fill="none" stroke="var(--lime)"/><path d="M0.5,2 L5,5.5 L9.5,2" fill="none" stroke="var(--lime)"/></svg>dmoreau@kelvorstruct.com</li>
        <li><svg viewBox="0 0 10 10"><circle cx="5" cy="5" r="4.3" fill="none" stroke="var(--lime)"/><path d="M0.7,5 H9.3 M5,0.7 C2.5,3 2.5,7 5,9.3 M5,0.7 C7.5,3 7.5,7 5,9.3" fill="none" stroke="var(--lime)" stroke-width=".8"/></svg>www.kelvorstruct.com</li>
      </ul>
    </div>
  </section>

  <section class="card card--back" aria-label="Business card back">
    <div class="back__brand">Kelvor</div>
    <div class="back__cities">DENVER<span class="sep">/</span>COLUMBUS<span class="sep">/</span>PHOENIX<span class="sep">/</span>RALEIGH</div>
  </section>
</body>
</html>
```